Tidy paddock Services

After a high quality design website. we are a company that provides services to people that own land and need a hand getting on top of the delayed jobs.
would want a number of tab/ pages for the web page.
Home page / About us page / services page / Gallery page. / Contact us page
we offer a wide range of services .listed below

Stock Work (title)

Stock movement
Break feeding
Temporary staffing

Spraying (title)

Spraying weeds
Spraying gorse

Pastures (title)

Fertilizing
Topping

Building (title)

Habitable sheds
Farm sheds
Sheep yards
Cattle yards
Repair farm buildings
Decks
Retaining walls

Fencing (title)

Stock fencing
Post & rail
Stock yards repair
Electric fencing install & repairs

Water Management (title)

Water trough installation
Water scheme install
Water trough cleaning
Farm water maintenance
Water ponds
Ornamental ponds
Drainage

General (title)

Lawn mowing
Hedge trimming
Pruning trees
Metaling drive ways & races
Water blasting
Small digger work
Little tip truck cartage
Home kill management
Mulching gorse
Section clearing

```html
<!DOCTYPE html>
<html lang="en">
<head>
<meta charset="utf-8">
<title>Tidy paddock Services</title>
<link href="https://fonts.googleapis.com/css2?family=Lato:wght@400;700&family=Montserrat:wght@500;600;700;800&display=swap" rel="stylesheet">
<style>
:root{
  --green:#64a10f;
  --green-dark:#4d7f0a;
  --black:#0a0a0a;
  --ink:#111111;
  --text:#555555;
  --white:#ffffff;
  --field:#ffffff;
}
*{margin:0;padding:0;box-sizing:border-box}
html,body{width:1200px;height:3669px;overflow:hidden;background:var(--white)}
body{font-family:'Lato',sans-serif;color:var(--ink)}
.page{position:relative;width:1200px;height:3669px;overflow:hidden}
.abs{position:absolute}

/* header */
.brand{position:absolute;display:flex;align-items:center;gap:12px}
.brand-dot{width:30px;height:30px;border-radius:50%;background:var(--green);flex:none}
.brand-name{font-family:'Montserrat',sans-serif;font-weight:600;color:var(--green);font-size:24px;line-height:1.1;width:210px}
.header-line{left:0;top:152px;width:400px;height:4px;background:var(--green)}
.contact-chip{position:absolute;top:21px;display:flex;align-items:center;gap:15px}
.chip-icon{width:52px;height:52px;border-radius:50%;background:var(--black);display:flex;align-items:center;justify-content:center}
.chip-label{font-size:13px;color:var(--green);text-transform:uppercase}
.chip-value{font-weight:700;font-size:22px;color:var(--ink)}
.chip-value.small{font-size:17px}
.nav-bar{left:378px;top:94px;width:822px;height:63px}
.main-nav{position:absolute;top:94px;height:63px;left:0;width:1200px}
.main-nav a,.foot-nav a{position:absolute;transform:translateX(-50%);text-decoration:none;white-space:nowrap;font-size:20px}
.main-nav a{top:20px;color:var(--white)}

/* hero */
.hero{left:0;top:157px;width:1200px;height:697px;
  background:radial-gradient(circle at 880px 230px,#4f7a26 0,#3a5e1c 180px,transparent 330px),
             linear-gradient(180deg,#1e2f14 0%,#2d4a1d 45%,#4f7c25 75%,#6a9a2f 100%)}
.hero-copy{left:105px;top:225px;color:var(--white);font-family:'Montserrat',sans-serif;font-weight:700}
.hero-kicker{font-size:58px;line-height:1}
.hero-title{font-size:88px;line-height:1.17;margin-top:14px}
.hero-sub{left:105px;top:534px;color:var(--white);font-size:20px}
.btn{position:absolute;display:flex;align-items:center;gap:9px;border-radius:22px;font-weight:700;font-size:17px;text-decoration:none;padding:0 18px 0 22px;height:40px}
.btn-green{background:var(--green);color:var(--white)}
.btn-white{background:var(--white);color:var(--green)}

/* about */
.about-photo{left:157px;top:983px;width:412px;height:412px;border-radius:50%;
  background:radial-gradient(circle at 60% 40%,#e9ecee 0,#b9c7b4 18%,#5f8f3c 45%,#2f5a1f 80%);box-shadow:0 0 22px rgba(0,0,0,.18)}
.section-title{font-family:'Montserrat',sans-serif;font-weight:800;font-size:46px;color:var(--ink);white-space:nowrap}
.section-title .accent{color:var(--green)}
.title-rule{height:2px;background:var(--green)}
.about-copy{left:630px;top:1057px;width:460px;font-size:14.5px;line-height:30px;color:var(--text)}
.about-copy p+p{margin-top:30px}

/* services */
.services-band{left:0;top:1594px;width:1200px;height:840px;
  background:linear-gradient(180deg,#5f9a13 0%,#5a9115 35%,#4f8419 65%,#5e9a16 100%)}
.services-title{color:var(--white)}
.lede{font-size:15px;text-align:center;width:1200px;left:0}
.service{position:absolute;width:228px;height:228px;border-radius:50%}
.service-label{position:absolute;left:22px;top:140px;width:184px;height:34px;background:rgba(255,255,255,.92);outline:1px solid #fff;outline-offset:3px;
  display:flex;align-items:center;justify-content:center;font-size:14.5px;font-weight:700;color:var(--ink);text-transform:uppercase}

/* contact */
.field{position:absolute;background:var(--field);border-radius:26px;box-shadow:0 2px 14px rgba(0,0,0,.09);font-size:14px;color:#555;padding:17px 33px}
.submit{position:absolute;left:624px;top:2932px;width:391px;height:53px;border-radius:27px;background:var(--green);color:var(--white);
  font-weight:700;font-size:18px;display:flex;align-items:center;justify-content:center}

/* footer */
.footer-base{left:0;top:3250px;width:1200px;height:419px;background:var(--black)}
.foot-nav a{top:3489px;color:var(--white)}
.social{position:absolute;top:3549px;width:34px;height:34px;border-radius:50%;background:var(--green)}
.copyright{left:0;width:1200px;top:3611px;text-align:center;color:var(--white);font-size:11px}
.footer-rule{left:0;top:3665px;width:1200px;height:4px;background:var(--green)}
</style>
</head>
<body>
<div class="page">

  <div class="abs hero" role="img" aria-label="Photo of a rounded green hedge on a mown lawn"></div>

  <div class="abs" style="left:0;top:0;width:1200px;height:157px;background:var(--white)"></div>
  <div class="brand" style="left:85px;top:48px">
    <span class="brand-dot"></span>
    <span class="brand-name">Tidy paddock Services</span>
  </div>
  <div class="abs header-line"></div>
  <svg class="abs nav-bar" viewBox="0 0 822 63" aria-hidden="true"><polygon points="16,0 822,0 822,63 0,63" fill="var(--green)"/></svg>

  <div class="contact-chip" style="left:486px">
    <span class="chip-icon"><svg width="20" height="20" viewBox="0 0 24 24"><path fill="#fff" d="M6.6 10.8a15.1 15.1 0 0 0 6.6 6.6l2.2-2.2a1 1 0 0 1 1-.25 11.4 11.4 0 0 0 3.6.57 1 1 0 0 1 1 1V20a1 1 0 0 1-1 1A17 17 0 0 1 3 4a1 1 0 0 1 1-1h3.5a1 1 0 0 1 1 1c0 1.25.2 2.45.57 3.57a1 1 0 0 1-.25 1z"/></svg></span>
    <div><div class="chip-label">Call us:</div><div class="chip-value">+1 555 014 2290</div></div>
  </div>
  <div class="contact-chip" style="left:779px">
    <span class="chip-icon"><svg width="20" height="16" viewBox="0 0 24 18"><path fill="#fff" d="M0 2l12 8 12-8V0H0zm0 3v13h24V5L12 13z"/></svg></span>
    <div><div class="chip-label">Email us:</div><div class="chip-value small">info@tidypaddockservices.com</div></div>
  </div>

  <nav class="main-nav">
    <a href="#" style="left:445px">Home</a>
    <a href="#" style="left:578px">About Us</a>
    <a href="#" style="left:740px">Our Services</a>
    <a href="#" style="left:894px">Gallery</a>
    <a href="#" style="left:1040px">Contact Us</a>
  </nav>

  <div class="abs hero-copy">
    <div class="hero-kicker">WELCOME TO</div>
    <div class="hero-title">TIDY PADDOCK<br>SERVICES</div>
  </div>
  <div class="abs hero-sub">Sed ut perspiciatis unde omnis iste natus error sit voluptatem accusantium</div>
  <a class="btn btn-green" href="#" style="left:131px;top:586px">Contact Us
    <svg width="15" height="15" viewBox="0 0 16 16"><circle cx="8" cy="8" r="8" fill="#fff"/><path d="M6.5 4.5 10 8l-3.5 3.5" stroke="var(--green)" stroke-width="2" fill="none"/></svg></a>
  <a class="btn btn-white" href="#" style="left:325px;top:586px">View Services
    <svg width="15" height="15" viewBox="0 0 16 16"><circle cx="8" cy="8" r="8" fill="var(--green)"/><path d="M6.5 4.5 10 8l-3.5 3.5" stroke="#fff" stroke-width="2" fill="none"/></svg></a>

  <svg class="abs" style="left:0;top:640px" width="1200" height="220" viewBox="0 0 1200 220" aria-hidden="true">
    <path d="M0 214 L0 130 C150 60 300 55 440 85 C560 112 650 150 700 165 C880 215 1060 210 1200 160 L1200 220 Z" fill="#fff"/>
    <path d="M0 214 C60 140 200 95 330 95 C460 95 580 130 672 160 C560 118 420 80 310 75 C180 70 60 95 0 130 Z" fill="var(--black)"/>
    <path d="M600 148 C780 200 980 200 1200 90 L1200 125 C1040 195 840 215 640 168 Z" fill="var(--green)"/>
    <path d="M610 155 C800 190 1000 170 1200 60 L1200 68 C1000 180 800 200 610 160 Z" fill="#fff"/>
  </svg>

  <div class="abs about-photo" role="img" aria-label="Photo of a white picket fence bordered by garden shrubs"></div>

  <div class="abs section-title" style="left:630px;top:958px">ABOUT <span class="accent">US</span></div>
  <div class="abs title-rule" style="left:630px;top:1031px;width:143px"></div>
  <div class="abs about-copy">
    <p>I must explain to you how all this mistaken idea of denouncing pleasure and praising pain was born and I will give you a complete account of the system, and expound the actual teachings of the great explorer of the truth, the master-builder of human happiness.</p>
    <p>No one rejects, dislikes, or avoids pleasure itself, because it is pleasure, but because those who do not know how to pursue pleasure rationally encounter consequences that are extremely painful. Nor again is there anyone who loves or pursues or desires to obtain pain</p>
  </div>
  <a class="btn btn-green" href="#" style="left:648px;top:1372px">Read More
    <svg width="15" height="15" viewBox="0 0 16 16"><circle cx="8" cy="8" r="8" fill="#fff"/><path d="M6.5 4.5 10 8l-3.5 3.5" stroke="var(--green)" stroke-width="2" fill="none"/></svg></a>

  <svg class="abs" style="left:0;top:1580px" width="1200" height="20" viewBox="0 0 1200 20" aria-hidden="true">
    <path d="M50 16 C120 0 1080 0 1160 16 Z" fill="var(--black)"/></svg>
  <div class="abs services-band" role="img" aria-label="Green-tinted photo of open farmland"></div>
  <svg class="abs" style="left:0;top:2432px" width="1200" height="16" viewBox="0 0 1200 16" aria-hidden="true">
    <path d="M50 0 C120 14 1080 14 1160 0 Z" fill="var(--black)"/></svg>

  <div class="abs section-title services-title" style="left:0;width:1200px;text-align:center;top:1693px">OUR SERVICES</div>
  <div class="abs title-rule" style="left:529px;top:1765px;width:143px;background:#fff"></div>
  <div class="abs lede" style="top:1799px;color:#fff">Lorem ipsum dolor sit amet, consectetur adipiscing elit, sed do eiusmod tempor incididunt ut labore et dolore</div>

  <div class="service" style="left:114px;top:1868px;background:radial-gradient(circle at 40% 35%,#e0c48a,#c49a4a 55%,#8a6526)" role="img" aria-label="Photo of hands over a golden grain field"><span class="service-label">Stock Work</span></div>
  <div class="service" style="left:363px;top:1868px;background:radial-gradient(circle at 55% 45%,#9dbd70,#4f7d2b 60%,#2c3c22)" role="img" aria-label="Photo of a worker spraying weeds"><span class="service-label">Spraying</span></div>
  <div class="service" style="left:609px;top:1868px;background:linear-gradient(180deg,#d9d8cf 0%,#b8a774 30%,#7fa23a 55%,#5b8a24 100%)" role="img" aria-label="Photo of green pasture with hills"><span class="service-label">Pastures</span></div>
  <div class="service" style="left:858px;top:1868px;background:radial-gradient(circle at 50% 40%,#c9d0c9,#8aa35c 50%,#5c7f2e)" role="img" aria-label="Photo of a farmer with sheep beside a farm building"><span class="service-label">Building</span></div>
  <div class="service" style="left:238px;top:2100px;background:linear-gradient(120deg,#8a6a45 0%,#a98460 45%,#c56aa8 70%,#6b8f3c 100%)" role="img" aria-label="Photo of a timber fence with flowers"><span class="service-label">Fencing</span></div>
  <div class="service" style="left:487px;top:2100px;background:linear-gradient(180deg,#5b86c0 0%,#4f6b3a 40%,#6a4a35 65%,#8aa0a8 100%)" role="img" aria-label="Photo of a garden pond with rocks and trees"><span class="service-label">Water Management</span></div>
  <div class="service" style="left:733px;top:2100px;background:linear-gradient(135deg,#5b5a7a 0%,#4f7d35 45%,#c9b89a 60%,#5f8f32 100%)" role="img" aria-label="Aerial photo of a mower on a lawn by a path"><span class="service-label">General</span></div>

  <div class="abs section-title" style="left:0;width:1200px;text-align:center;top:2533px">GET IN TOUCH <span class="accent">WITH US</span></div>
  <div class="abs title-rule" style="left:529px;top:2607px;width:143px"></div>
  <div class="abs lede" style="top:2642px;color:var(--text)">Lorem ipsum dolor sit amet, consectetur adipiscing elit, sed do eiusmod tempor incididunt ut labore et dolore</div>

  <div class="field" style="left:185px;top:2706px;width:396px;height:54px">First Name</div>
  <div class="field" style="left:185px;top:2782px;width:396px;height:54px">Last Name</div>
  <div class="field" style="left:185px;top:2857px;width:396px;height:54px">Contact Number</div>
  <div class="field" style="left:185px;top:2932px;width:396px;height:54px">Email Address</div>
  <div class="field" style="left:617px;top:2706px;width:398px;height:202px;border-radius:24px">Messages</div>
  <div class="submit">Submit Here</div>

  <svg class="abs" style="left:0;top:3135px" width="1200" height="130" viewBox="0 0 1200 130" aria-hidden="true">
    <path d="M0 12 C120 110 400 130 660 70 C860 30 1060 35 1200 90 L1200 130 L0 130 Z" fill="var(--black)"/>
    <path d="M0 40 C160 120 420 118 660 60 C420 105 180 105 0 48 Z" fill="#fff"/>
    <path d="M680 58 C880 20 1080 30 1200 100 L1200 125 C1090 60 900 40 680 58 Z" fill="var(--green)"/>
  </svg>
  <div class="abs footer-base" role="img" aria-label="Dark photo of farmland at night"></div>

  <div class="brand" style="left:460px;top:3382px">
    <span class="brand-dot"></span>
    <span class="brand-name" style="width:auto;white-space:nowrap">Tidy paddock Services</span>
  </div>

  <nav class="foot-nav">
    <a href="#" style="left:292px">Home</a>
    <a href="#" style="left:424px">About Us</a>
    <a href="#" style="left:586px">Our Services</a>
    <a href="#" style="left:740px">Gallery</a>
    <a href="#" style="left:887px">Contact Us</a>
  </nav>
  <span class="social" style="left:543px" aria-label="Social link 1"></span>
  <span class="social" style="left:584px" aria-label="Social link 2"></span>
  <span class="social" style="left:624px" aria-label="Social link 3"></span>
  <div class="abs copyright">(C) Copyright 2024 | All Rights Reserved</div>
  <div class="abs footer-rule"></div>

</div>
</body>
</html>
```